OpenHarbor Yoga Website Design

Business Logo - attached
5 pages being:
Home
About
Classes
Blog
Contact

Would like Scrolling webpage and yoga symbols to be used.

Must have's being:
Easy to navigate, Text needs to be able to be edited/updated, Enquire Now Links, More Information Links, be a secure site, SEO,

Please refer to attached document for the information for the body of the website.

Target Market(s)

Educators, Community Service, Health and Wellbeing, Mental Health

Industry/Entity Type

Yoga

Coding

Coded - Design and coding required

Number of Pages Required

5+ page

Font styles to use
Other font styles liked:
• Bella Bold BC

Colors
0094D4
00A9DD
6FCCEA
C7EBF8
E9F6FB
6B429C
8869AF
B7A5CE
E3DAEB
F3F0F8

Requirements
Must have
• Easy to navigate, Text needs to be able to be edited/updated, Enquire Now Links, More Information Links, be a secure site, SEO,
Nice to have
• Scrolling webpage, yoga symbols

```html
<!DOCTYPE html>
<html lang="en">
<head>
<meta charset="utf-8">
<title>OpenHarbor Yoga</title>
<link rel="stylesheet" href="https://fonts.googleapis.com/css2?family=Poppins:wght@400;500;600&family=Kaushan+Script&family=Domine:wght@400;600&display=swap">
<style>
:root{
  --blue:#0094D4;
  --blue-2:#00A9DD;
  --blue-3:#6FCCEA;
  --blue-4:#C7EBF8;
  --purple:#6B429C;
  --purple-2:#8869AF;
  --purple-3:#B7A5CE;
  --purple-4:#E3DAEB;
  --purple-5:#F3F0F8;
  --ink:#2a2a2a;
  --white:#ffffff;
}
*{box-sizing:border-box;margin:0;padding:0}
html,body{width:1200px;height:4569px;overflow:hidden}
body{position:relative;background:var(--white);font-family:"Poppins",sans-serif;color:var(--ink);font-size:15px;line-height:1.85}
.abs{position:absolute}
.script{font-family:"Kaushan Script",cursive;font-weight:400}
.script .accent{color:var(--blue)}

/* header */
.header{left:0;top:0;width:1200px;height:147px;background:var(--white);z-index:1}
.brand{left:79px;top:5px;width:150px;height:150px;border-radius:50%;background:var(--white);display:flex;align-items:center;justify-content:center;text-align:center;z-index:4;font-weight:500;color:var(--purple-2);font-size:17px;line-height:1.3}
.contact-item{display:flex;align-items:center;gap:12px;font-family:"Domine",serif;font-weight:600;color:var(--purple);font-size:18px;top:26px;z-index:5;white-space:nowrap}
.icon-dot{width:38px;height:38px;border-radius:50%;background:var(--blue);display:flex;align-items:center;justify-content:center;flex:none}
.nav{right:73px;top:96px;display:flex;gap:29px;font-family:"Domine",serif;font-size:19px;font-weight:600;color:#222;z-index:5;line-height:1.4}
.nav a{color:inherit;text-decoration:none}
.nav .current{color:var(--blue)}

/* hero */
.hero{left:0;top:147px;width:1200px;height:668px;border-radius:0 0 150px 150px;overflow:hidden;background:linear-gradient(180deg,#7c8a7e 0%,#a49a8c 45%,#6b5a6a 100%)}
.hero-title{left:0;width:1200px;top:335px;text-align:center;color:var(--white);font-size:118px;line-height:1.2;white-space:nowrap}
.hero-actions{left:0;width:1200px;top:510px;display:flex;justify-content:center;gap:30px}
.btn{display:inline-flex;align-items:center;justify-content:center;height:56px;border-radius:28px;background:linear-gradient(180deg,var(--blue),var(--purple));color:var(--white);font-weight:600;font-size:16px;text-decoration:none}
.btn-hero{width:234px;height:64px;border:3px solid var(--white);border-radius:32px;font-size:19px}
.btn-sm{width:194px}

/* welcome */
.welcome-art{left:70px;top:895px;width:500px;height:520px;border-radius:50%;background:radial-gradient(circle,var(--purple-4) 0%,var(--purple-3) 55%,rgba(183,165,206,0) 72%)}
.welcome{left:617px;top:885px;width:516px}
.h2{font-size:50px;line-height:1.4;color:#222;white-space:nowrap}
.welcome .h2{font-size:42px}
.welcome p{margin-top:14px;font-size:14.5px}

/* benefits */
.benefits{left:0;top:1507px;width:1200px;height:800px;background:var(--purple-5);border-radius:150px 150px 0 0}
.center{text-align:center}
.benefits-title{left:0;top:1560px;width:1200px}
.benefits-intro{left:80px;top:1652px;width:1040px}
.benefits-sub{left:0;top:1735px;width:1200px;color:var(--purple);font-size:40px}
.card{top:1849px;width:328px;height:244px;background:var(--white);border-radius:22px;text-align:center}
.card-icon{width:98px;height:98px;margin:34px auto 14px;border-radius:50%;background:var(--blue-4)}
.card-title{color:var(--blue);font-size:34px;white-space:nowrap}

/* detail panel */
.panel{left:0;top:2182px;width:1200px;height:2140px;background:var(--white);border-radius:150px 150px 0 0}
.h3{color:var(--purple);font-size:44px;line-height:1.3}
.ticks{list-style:none;font-size:15px}
.ticks li{position:relative;padding-left:33px;margin-bottom:15px;line-height:1.9}
.ticks li::before{content:"";position:absolute;left:0;top:7px;width:15px;height:15px;border-radius:50%;background:var(--purple)}
.ticks li::after{content:"";position:absolute;left:5px;top:10px;width:4px;height:7px;border:solid var(--white);border-width:0 2px 2px 0;transform:rotate(45deg)}
.photo{width:516px;height:516px;border-radius:50%;box-shadow:-12px 14px 0 var(--purple-2)}
.photo-bodies{background:linear-gradient(160deg,#e9eef2,#8fa7b8 60%,#c8b59f)}
.photo-minds{background:linear-gradient(160deg,#f1ebe2,#c9a58d 55%,#8d5044)}
.photo-spirits{background:radial-gradient(circle at 50% 35%,#9fd1e8 0%,#2d3f6e 40%,#1a1530 80%)}

.closing{left:70px;top:4050px;width:1060px;font-size:15px}

/* footer */
.footer{left:0;top:4316px;width:1200px;height:253px;background:var(--blue);border-radius:150px 150px 0 0}
.footer-brand{left:520px;top:4225px;width:160px;height:160px;border-radius:50%;background:var(--white);display:flex;align-items:center;justify-content:center;text-align:center;font-weight:500;color:var(--purple-2);font-size:16px;line-height:1.3;z-index:2}
.footer-mail{left:0;top:4395px;width:1200px;display:flex;justify-content:center;align-items:center;gap:14px;font-family:"Domine",serif;font-weight:600;color:var(--white);font-size:19px}
.footer-mail .icon-dot{background:var(--white)}
.copyright{left:0;top:4459px;width:1200px;text-align:center;color:var(--white);font-size:14px}
.social{left:0;top:4496px;width:1200px;display:flex;justify-content:center;gap:20px}
.social span{width:22px;height:22px;border-radius:50%;background:var(--white)}
</style>
</head>
<body>

<header class="abs header"></header>
<div class="abs brand">OpenHarbor<br>Yoga</div>
<div class="abs contact-item" style="left:617px">
  <span class="icon-dot"><svg width="18" height="18" viewBox="0 0 24 24"><path fill="#fff" d="M6.6 10.8a15 15 0 0 0 6.6 6.6l2.2-2.2a1 1 0 0 1 1-.25 11.4 11.4 0 0 0 3.6.57 1 1 0 0 1 1 1V20a1 1 0 0 1-1 1A17 17 0 0 1 3 4a1 1 0 0 1 1-1h3.5a1 1 0 0 1 1 1c0 1.25.2 2.45.57 3.6a1 1 0 0 1-.25 1z"/></svg></span>
  0400 123 456
</div>
<div class="abs contact-item" style="left:805px">
  <span class="icon-dot"><svg width="18" height="18" viewBox="0 0 24 24"><path fill="#fff" d="M3 6h18v12H3z"/><path fill="none" stroke="#0094D4" stroke-width="2" d="M3 6l9 7 9-7"/></svg></span>
  info@openharboryoga.com.au
</div>
<nav class="abs nav"><a class="current" href="#">Home</a><a href="#">About</a><a href="#">Classes</a><a href="#">Blog</a><a href="#">Contact</a></nav>

<section class="abs hero" role="img" aria-label="Photo of a yoga class with people seated on mats, arms raised overhead"></section>
<h1 class="abs hero-title script">OpenHarbor Yoga</h1>
<div class="abs hero-actions">
  <a class="btn btn-hero" href="#">Enquire Now</a>
  <a class="btn btn-hero" href="#">More Information</a>
</div>

<div class="abs welcome-art" role="img" aria-label="Large purple yoga figure symbol surrounded by dots"></div>
<section class="abs welcome">
  <h2 class="h2 script">Welcome to <span class="accent">OpenHarbor Yoga</span></h2>
  <p>OpenHarbor Yoga believe that you are never too young to benefit from and fall in love with yoga.&nbsp; My aim is to EMPOWER kids and teens to thrive by teaching life skills in Yoga, Mindfulness and Breathing techniques to deal with daily challenges and big emotions.</p>
  <p>OpenHarbor Yoga gives kids an opportunity to enjoy and experience yoga for themselves and primarily focuses on programs for Schools, Pre Schools and Early Learning Centres, Private Classes, Sporting Clubs, Martial Arts Schools, Scout Groups and Occupational Therapy Centres just to name a few.<br>All classes are age appropriate and encourage children’s natural drive to learn, move, and be creative.</p>
  <a class="btn btn-sm" href="#" style="margin-top:22px">Read More</a>
</section>

<section class="abs benefits"></section>
<h2 class="abs h2 script benefits-title center">Benefits of <span class="accent">Yoga</span></h2>
<p class="abs benefits-intro center">The benefits of yoga can last a lifetime. It is my aim &amp; passion to introduce yoga to kids of all ages and backgrounds so that they can not only experience the benefits of yoga but fall in love with the practice.</p>
<h3 class="abs benefits-sub script center">Yoga benefits include</h3>
<div class="abs card" style="left:74px"><div class="card-icon" role="img" aria-label="Healthy body icon"></div><div class="card-title script">Healthy Bodies</div></div>
<div class="abs card" style="left:436px"><div class="card-icon" role="img" aria-label="Healthy mind icon"></div><div class="card-title script">Healthy Mind</div></div>
<div class="abs card" style="left:799px"><div class="card-icon" role="img" aria-label="Healthy spirit icon"></div><div class="card-title script">Healthy Spirits</div></div>

<section class="abs panel"></section>

<div class="abs" style="left:74px;top:2280px;width:500px">
  <h3 class="h3 script">Healthy Bodies</h3>
  <ul class="ticks" style="margin-top:14px">
    <li>Develops strong, flexible and healthy bodies</li>
    <li>Promotes spinal alignment and good posture</li>
    <li>Builds energy and stamina</li>
    <li>Improves internal physical function – organs, digestion, elimination, circulation, and blood flow.</li>
    <li>Helps breathing and lung capacity</li>
    <li>Teaches the enjoyment of movement</li>
    <li>Works the ‘whole’ body</li>
  </ul>
  <a class="btn btn-sm" href="#" style="margin-top:14px">Read More</a>
</div>
<div class="abs photo photo-bodies" style="left:612px;top:2277px" role="img" aria-label="Photo of a smiling man stretching in a group yoga class"></div>

<div class="abs photo photo-minds" style="left:75px;top:2856px" role="img" aria-label="Photo of a woman meditating cross-legged"></div>
<div class="abs" style="left:617px;top:2870px;width:520px">
  <h3 class="h3 script">Healthy Minds</h3>
  <ul class="ticks" style="margin-top:14px">
    <li>Cultivates confidence and self-esteem</li>
    <li>Develops concentration and attention</li>
    <li>Clears the mind for better clarity and decision making</li>
    <li>Helps relax and sleep better</li>
    <li>Calms the nervous system</li>
    <li>Learns to cope with stressful situations</li>
    <li>Balances emotions</li>
  </ul>
  <a class="btn btn-sm" href="#" style="margin-top:52px">Read More</a>
</div>

<div class="abs" style="left:74px;top:3462px;width:500px">
  <h3 class="h3 script">Healthy Spirits</h3>
  <ul class="ticks" style="margin-top:14px">
    <li>Fosters creativity, expression and imagination</li>
    <li>Cultivates kindness to themselves and others</li>
    <li>Cultivates respect for self and others</li>
    <li>Builds balance and inner quiet</li>
    <li>Builds inner strength and resilience</li>
    <li>Teaches self-awareness</li>
    <li>Focuses on positive self-talk</li>
  </ul>
  <a class="btn btn-sm" href="#" style="margin-top:52px">Read More</a>
</div>
<div class="abs photo photo-spirits" style="left:612px;top:3455px" role="img" aria-label="Illustration of a meditating figure glowing against a starry cosmos"></div>

<div class="abs closing center">
  <p>OpenHarbor Yoga combines all the benefits of traditional yoga and a lot of fun!<br>We play games and practice engaging flows which get our bodies moving, then we take a quiet moment to be still and calm as we focus on our breathing.</p>
  <p style="margin-top:6px">OpenHarbor Yoga Kids will learn that relaxation is just as important as moving their bodies, and the exercises which they learn in class can easily be repeated at any time in their busy day to feel calm and grounded.</p>
</div>

<footer class="abs footer"></footer>
<div class="abs footer-brand">OpenHarbor<br>Yoga</div>
<div class="abs footer-mail">
  <span class="icon-dot"><svg width="18" height="18" viewBox="0 0 24 24"><path fill="#0094D4" d="M3 6h18v12H3z"/><path fill="none" stroke="#fff" stroke-width="2" d="M3 6l9 7 9-7"/></svg></span>
  info@openharboryoga.com.au
</div>
<p class="abs copyright">© Copyrights 2023. OpenHarbor Yoga All Rights Reserved</p>
<div class="abs social"><span aria-label="Social link"></span><span aria-label="Social link"></span></div>

</body>
</html>
```